Realty Group Needs Classy, Contemporary Letterhead Design

We need a letterhead design for a new realty company located in NY, USA. We buy investment properties to rehabilitate and or keep in our rental portfolio.

```html
<!DOCTYPE html>
<html lang="en">
<head>
<meta charset="utf-8">
<title>Meridian Realty Group Letterhead</title>
<link rel="stylesheet" href="https://fonts.googleapis.com/css2?family=Open+Sans:wght@400;600&family=Lato:wght@400&display=swap">
<style>
  :root {
    --brand-purple: #4f2a85;
    --ink: #3a3a3a;
    --ink-strong: #2d2d2d;
    --paper: #ffffff;
    --signature-tone: #dedbe4;
  }
  html, body {
    margin: 0;
    padding: 0;
    width: 1040px;
    height: 1200px;
    overflow: hidden;
    background: var(--paper);
  }
  .letterhead {
    position: relative;
    width: 1040px;
    height: 1200px;
    background: var(--paper);
    font-family: "Open Sans", Arial, sans-serif;
    color: var(--ink);
  }
  .wave { position: absolute; left: 0; width: 1040px; display: block; }
  .wave-top { top: 0; height: 180px; }
  .wave-bottom { bottom: 0; height: 200px; }

  .company-name {
    position: absolute;
    top: 84px;
    right: 101px;
    margin: 0;
    font-size: 22px;
    font-weight: 600;
    line-height: 28px;
    color: var(--brand-purple);
    white-space: nowrap;
  }

  .letter-block {
    position: absolute;
    left: 98px;
    width: 842px;
    margin: 0;
    font-size: 16.5px;
  }
  .issue-date { top: 213px; line-height: 26px; }
  .recipient { top: 253px; line-height: 18px; }
  .salutation { top: 353px; line-height: 26px; }
  .paragraph { text-align: justify; line-height: 27px; }
  .paragraph-1 { top: 406px; }
  .paragraph-2 { top: 567px; }
  .paragraph-3 { top: 675px; }
  .closing { top: 812px; line-height: 26px; }
  .signature {
    position: absolute;
    left: 98px;
    top: 851px;
    width: 240px;
    height: 28px;
    background: var(--signature-tone);
    border-radius: 3px;
  }
  .signer-name {
    top: 892px;
    font-size: 19px;
    line-height: 24px;
    font-weight: 600;
    color: var(--ink-strong);
  }
  .signer-title { top: 920px; line-height: 24px; }

  .contact {
    position: absolute;
    right: 88px;
    top: 1078px;
    text-align: right;
    font-family: "Lato", Arial, sans-serif;
    color: var(--paper);
  }
  .contact-line {
    display: flex;
    justify-content: flex-end;
    align-items: center;
    gap: 8px;
    font-size: 18px;
    line-height: 19px;
  }
  .contact-line svg { width: 15px; height: 15px; }
  .contact-address {
    margin-top: 13px;
    margin-right: -22px;
    font-size: 18px;
  }
</style>
</head>
<body>
<main class="letterhead">
  <svg class="wave wave-top" viewBox="0 0 1040 180" preserveAspectRatio="none" aria-hidden="true">
    <path fill="var(--brand-purple)" d="M0,0 H1040 V140 C990,60 900,18 770,30 C620,45 520,135 380,137 C230,140 110,95 0,40 Z"/>
    <path fill="none" stroke="var(--paper)" stroke-width="5" d="M0,46 C110,98 230,124 370,122 C520,118 610,40 770,14 C890,-4 975,30 1020,72"/>
  </svg>

  <p class="company-name">Meridian Realty Group, LLC</p>

  <p class="letter-block issue-date">Issuing Date: May 5, 2018</p>
  <p class="letter-block recipient">Name Of Employee Mr. XYZABC<br>Address of Employee<br>Address Line 2 etc..</p>
  <p class="letter-block salutation">Dear Mr.XYZABC</p>
  <p class="letter-block paragraph paragraph-1">Lorem Ipsum has been the industry's standard dummy text ever since the 1500s, when an unknown printer took a galley of type and scrambled it to make a type specimen book. It has survived not only five centuries, but also the leap into electronic typesetting, remaining essentially unchanged. It was popularised in the 1960s with the release of Letraset sheets containing Lorem Ipsum passages, and more recently with desktop publishing software like Aldus PageMaker including versions of Lorem Ipsum.</p>
  <p class="letter-block paragraph paragraph-2">Lorem Ipsum is simply dummy text of the printing and typesetting industry. Lorem Ipsum has been the industry's standard dummy text ever since the 1500s, when an unknown printer took a galley of type and scrambled it to make a type specimen book.</p>
  <p class="letter-block paragraph paragraph-3">It has survived not only five centuries, but also the leap into electronic typesetting, remaining essentially unchanged. It was popularised in the 1960s with the release of Letraset sheets containing Lorem IpsumIpsum passages.</p>
  <p class="letter-block closing">Yours Sincerely</p>
  <span class="signature" role="img" aria-label="Handwritten signature of Daniel Harper"></span>
  <p class="letter-block signer-name">Daniel Harper</p>
  <p class="letter-block signer-title">Managing Director</p>

  <svg class="wave wave-bottom" viewBox="0 0 1040 200" preserveAspectRatio="none" aria-hidden="true">
    <path fill="var(--brand-purple)" d="M0,87 C60,130 160,168 290,166 C460,162 560,40 720,8 C850,-14 970,30 1040,80 V200 H0 Z"/>
    <path fill="none" stroke="var(--paper)" stroke-width="5" d="M30,135 C110,168 200,178 300,172 C460,160 570,60 720,22 C850,-8 960,30 1040,70"/>
  </svg>

  <footer class="contact">
    <div class="contact-line">212-555 0148
      <svg viewBox="0 0 16 16" aria-hidden="true"><path fill="var(--paper)" d="M3 2h3l1.5 3.5-2 1.2a8 8 0 0 0 3.8 3.8l1.2-2L14 10v3a1.5 1.5 0 0 1-1.5 1.5A11.5 11.5 0 0 1 1.5 3.5 1.5 1.5 0 0 1 3 2z"/></svg>
    </div>
    <div class="contact-line">info@meridianrealty.com
      <svg viewBox="0 0 16 16" aria-hidden="true"><rect x="1" y="3" width="14" height="10" fill="var(--paper)"/><path d="M1.5 3.5 8 9l6.5-5.5" fill="none" stroke="var(--brand-purple)" stroke-width="1.3"/></svg>
    </div>
    <div class="contact-line">www.meridianrealty.com
      <svg viewBox="0 0 16 16" aria-hidden="true"><circle cx="8" cy="8" r="7" fill="var(--paper)"/><path d="M1 8h14M8 1c-3 3.5-3 10.5 0 14M8 1c3 3.5 3 10.5 0 14" fill="none" stroke="var(--brand-purple)" stroke-width="1"/></svg>
    </div>
    <div class="contact-address">88 Hudson Street, New York, NY 10013</div>
  </footer>
</main>
</body>
</html>
```